Maplewind Farms - business cards
Business Card
Project: Maplewind Farms - business cards
Maplewind Farms - business cards - Agriculture
Creative Brief
Use same font as used in my logo
Neil Hartman
38157 Copper Fern Lane Cheney, WA 99004
nhartman@birchgate-equity.example
Can I see the design for a one sided card vs a 2 sided card? I want to send to the printer to see how much more it costs for 2 sided.
we might just do one sided; for a two sided card, just the logo

```html
<!DOCTYPE html>
<html lang="en">
<head>
<meta charset="utf-8">
<title>Maplewind Farms – Business Cards</title>
<link href="https://fonts.googleapis.com/css2?family=Libre+Baskerville:wght@400;700&display=swap" rel="stylesheet">
<style>
  :root {
    --backdrop: #e6e6e4;
    --card: #fbfbf9;
    --gold: #e0a526;
    --gold-light: #f0c55a;
    --brown: #9a6618;
    --ink: #2b2b2b;
    --name: #c98f1c;
  }
  * { margin: 0; padding: 0; box-sizing: border-box; }
  html, body {
    width: 1200px; height: 944px; overflow: hidden;
    background: var(--backdrop);
    font-family: "Libre Baskerville", "Times New Roman", serif;
  }
  .sheet {
    position: relative; width: 1200px; height: 944px;
    display: flex; flex-direction: column; align-items: center;
    justify-content: center; gap: 40px;
  }
  .card {
    position: relative; width: 700px; height: 400px;
    background: var(--card); overflow: hidden;
    box-shadow: 0 2px 6px rgba(0,0,0,.12);
  }
  .card-waves { position: absolute; inset: 0; width: 100%; height: 100%; }
  .wordmark {
    position: absolute; display: flex; align-items: center; gap: 10px;
    color: var(--gold); font-weight: 700; letter-spacing: 1px;
    text-transform: uppercase; line-height: 1; white-space: nowrap;
  }
  .wordmark-dot {
    width: 14px; height: 14px; border-radius: 50%; background: var(--gold); flex: none;
  }
  .card-back .wordmark {
    left: 50%; top: 50%; transform: translate(-50%, -50%); font-size: 38px;
  }
  .card-back .wordmark-dot { width: 18px; height: 18px; }
  .card-front .wordmark { right: 44px; top: 112px; font-size: 24px; }
  .contact { position: absolute; left: 52px; top: 58px; color: var(--ink); }
  .contact-name {
    color: var(--name); font-size: 24px; font-weight: 400; margin-bottom: 22px;
  }
  .contact-line {
    font-size: 14px; line-height: 1.55; display: flex; align-items: center; gap: 7px;
    white-space: nowrap;
  }
  .contact-address { margin-bottom: 2px; }
  .contact-icon { width: 12px; height: 12px; flex: none; }
</style>
</head>
<body>
<main class="sheet">

  <section class="card card-front" aria-label="Business card front">
    <svg class="card-waves" viewBox="0 0 700 400" aria-hidden="true">
      <path d="M0 270 C160 230 300 300 470 285 C580 275 650 250 700 238 L700 252 C640 266 580 290 470 300 C300 315 160 250 0 288 Z" fill="var(--gold-light)"/>
      <path d="M0 312 C170 270 320 335 480 320 C590 310 650 290 700 278 L700 400 L0 400 Z" fill="var(--gold)"/>
      <path d="M0 385 C180 360 380 390 700 330 L700 400 L0 400 Z" fill="var(--brown)"/>
      <path d="M0 370 C200 345 400 372 700 318 L700 330 C400 385 200 360 0 385 Z" fill="#fff" opacity=".35"/>
    </svg>

    <div class="contact">
      <h1 class="contact-name">Neil Hartman</h1>
      <p class="contact-line contact-address">38157 Copper Fern Lane</p>
      <p class="contact-line contact-address">Alder Springs, WA 99170</p>
      <p class="contact-line">
        <svg class="contact-icon" viewBox="0 0 12 12" aria-hidden="true"><rect x="3" y="0.5" width="6" height="11" rx="1.2" fill="var(--gold)"/><rect x="4.2" y="2" width="3.6" height="6" fill="#fff"/></svg>
        509.555.0148
      </p>
      <p class="contact-line">
        <svg class="contact-icon" viewBox="0 0 12 12" aria-hidden="true"><rect x="0.5" y="2.5" width="11" height="7.5" rx="1" fill="var(--gold)"/><path d="M1 3 L6 7 L11 3" stroke="#fff" stroke-width="1" fill="none"/></svg>
        nhartman@birchgate-equity.example
      </p>
    </div>

    <div class="wordmark"><span class="wordmark-dot"></span>Maplewind Farms</div>
  </section>

  <section class="card card-back" aria-label="Business card back">
    <div class="wordmark"><span class="wordmark-dot"></span>Maplewind Farms</div>
  </section>

</main>
</body>
</html>
```